Tech business card design

We need an amazing business card design for our new business 'Pexla' a marketing tech startup based in Sydney, Australia. We provide an online marketplace for businesses to search and buy advertising media, connect with service providers and learn more about marketing. We wish to communicate 'cool tech', reliability and professionalism and design based around our logo.

Target Market(s)

Business Owners

Contact Information for Business Card

Name
Position
Email Address
Website
Phone Number

Font styles to use
Other font styles liked:
• Avenir & Avenir Next

Colors

Designer to choose colors to be used in the design.

```html
<!DOCTYPE html>
<html lang="en">
<head>
<meta charset="utf-8">
<title>Pexla Business Card</title>
<link href="https://fonts.googleapis.com/css2?family=Nunito+Sans:wght@400;600;800&display=swap" rel="stylesheet">
<style>
  :root {
    --backdrop: #e9e9ea;
    --card: #f4f4f5;
    --navy: #1f1c45;
    --ink: #1f1c45;
    --white: #ffffff;
  }
  * { margin: 0; padding: 0; box-sizing: border-box; }
  html, body {
    width: 1200px; height: 800px; overflow: hidden;
    background: var(--backdrop);
    font-family: "Nunito Sans", "Avenir Next", Avenir, sans-serif;
    color: var(--ink);
  }
  .stage { position: relative; width: 1200px; height: 800px; }
  .card {
    position: absolute; top: 278px;
    width: 419px; height: 240px;
    background: var(--card);
    box-shadow: 0 2px 3px rgba(0,0,0,0.12);
  }
  .card--front { left: 142px; display: flex; align-items: center; justify-content: center; }
  .card--back { left: 638px; display: flex; }
  .wordmark { font-weight: 800; letter-spacing: -1px; line-height: 1; }
  .card--front .wordmark { font-size: 100px; color: var(--navy); margin-top: -4px; }
  .brand-panel {
    width: 209px; height: 100%;
    background: var(--navy);
    padding: 44px 0 0 34px;
  }
  .brand-panel .wordmark { font-size: 56px; color: var(--white); }
  .details { flex: 1; padding: 42px 0 0 23px; }
  .person-name { font-size: 21px; font-weight: 800; letter-spacing: 0.5px; line-height: 1.1; }
  .person-role { font-size: 14.5px; font-weight: 600; letter-spacing: 0.3px; margin-top: 1px; }
  .contact-list { list-style: none; margin-top: 50px; }
  .contact-list li {
    display: flex; align-items: center;
    font-size: 16px; font-weight: 600; height: 24px;
  }
  .contact-list svg { width: 13px; height: 13px; margin-right: 11px; fill: var(--ink); }
</style>
</head>
<body>
<main class="stage">
  <section class="card card--front">
    <span class="wordmark">pexla</span>
  </section>

  <section class="card card--back">
    <div class="brand-panel">
      <span class="wordmark">pexla</span>
    </div>
    <div class="details">
      <p class="person-name">JOHN SMITH</p>
      <p class="person-role">GENERAL MANAGER</p>
      <ul class="contact-list">
        <li>
          <svg viewBox="0 0 16 16" aria-hidden="true"><circle cx="8" cy="8" r="8"/><path d="M5.2 4.2l1.4-.3.8 2-1 .8c.5 1.2 1.4 2.1 2.6 2.6l.8-1 2 .8-.3 1.4c-.2.5-.7.8-1.3.7C7.4 10.8 5.2 8.6 4.5 5.5c-.1-.6.2-1.1.7-1.3z" fill="#f4f4f5"/></svg>
          012 345 6789
        </li>
        <li>
          <svg viewBox="0 0 16 16" aria-hidden="true"><rect x="0" y="2.5" width="16" height="11" rx="1.2"/><path d="M1 3.5l7 5 7-5" stroke="#f4f4f5" stroke-width="1.4" fill="none"/></svg>
          your@email.com
        </li>
        <li>
          <svg viewBox="0 0 16 16" aria-hidden="true"><circle cx="8" cy="8" r="8"/><g stroke="#f4f4f5" stroke-width="1" fill="none"><ellipse cx="8" cy="8" rx="3.2" ry="7"/><path d="M1 8h14M2.2 4.5h11.6M2.2 11.5h11.6"/></g></svg>
          www.website.com
        </li>
      </ul>
    </div>
  </section>
</main>
</body>
</html>
```